New LLC consulting company needs a business card design

I need a business card design for new company in Alexandria Virginia called TK Verdane Consulting LLC. The company is focused on consulting for defense and national security issues with expertise in nuclear and space topics. I would like to see designs that are simple and I am open to colors except for brown.

Target Market(s)

All businesses that are seeking consulting help

Industry/Entity Type

Consulting

Contact Information for Business Card

Name of company - TK Verdane Consulting LLC; name (Delia Pratt) President; email: prattdq47@mailvessa.com; Phone: 703-555-0142

Requirements
Must have
• The details described above
Nice to have
• I'm open to all ideas
Should not have
• No brown

```html
<!DOCTYPE html>
<html lang="en">
<head>
<meta charset="utf-8">
<title>Delia Pratt — TK Verdane Consulting LLC</title>
<link rel="stylesheet" href="https://fonts.googleapis.com/css2?family=Montserrat:wght@400;700&display=swap">
<style>
  :root {
    --page-bg: #999999;
    --card-bg: #ffffff;
    --ink: #000000;
    --ink-soft: #2b2b2b;
    --shadow: rgba(0, 0, 0, 0.6);
  }
  * { margin: 0; padding: 0; box-sizing: border-box; }
  html, body {
    width: 1200px;
    height: 1059px;
    overflow: hidden;
    background: var(--page-bg);
  }
  .business-card {
    position: absolute;
    left: 233px;
    top: 320px;
    width: 733px;
    height: 419px;
    background: var(--card-bg);
    border-radius: 26px;
    box-shadow: 14px 18px 30px var(--shadow);
    font-family: "Montserrat", sans-serif;
    text-align: center;
  }
  .company-name {
    position: absolute;
    left: 0; right: 0;
    top: 62px;
    font-size: 13px;
    font-weight: 700;
    color: var(--ink);
    letter-spacing: 3px;
    text-transform: uppercase;
    line-height: 1;
  }
  .card-name {
    position: absolute;
    left: 0; right: 0;
    top: 108px;
    font-size: 33px;
    font-weight: 700;
    color: var(--ink);
    letter-spacing: 0.2px;
    line-height: 1;
  }
  .card-title {
    position: absolute;
    left: 0; right: 0;
    top: 161px;
    font-size: 18px;
    font-weight: 400;
    color: var(--ink-soft);
    letter-spacing: 0.6px;
    line-height: 1;
  }
  .contact-divider {
    position: absolute;
    left: 260px;
    top: 199px;
    width: 212px;
    height: 30px;
  }
  .contact-line {
    position: absolute;
    left: 0; right: 0;
    font-weight: 400;
    color: var(--ink-soft);
    letter-spacing: 0.4px;
    line-height: 1;
  }
  .contact-email { top: 248px; font-size: 16.5px; }
  .contact-phone { top: 282px; font-size: 18px; letter-spacing: 0.6px; }
</style>
</head>
<body>
  <div class="business-card">
    <p class="company-name">TK Verdane Consulting LLC</p>
    <h1 class="card-name">Delia Pratt</h1>
    <p class="card-title">President</p>

    <svg class="contact-divider" viewBox="0 0 212 30" aria-hidden="true">
      <polygon class="divider-rule" points="0,15 30,13.6 60,14 60,16 30,16.4" fill="var(--ink)"/>
      <polygon class="divider-rule" points="152,14 182,13.6 212,15 182,16.4 152,16" fill="var(--ink)"/>
      <g class="icon-email">
        <circle cx="86" cy="15" r="14.5" fill="var(--ink)"/>
        <rect x="77" y="9" width="18" height="12" rx="1.5" fill="#fff"/>
        <polyline points="77.5,9.8 86,16 94.5,9.8" fill="none" stroke="var(--ink)" stroke-width="1.3"/>
        <line x1="77.5" y1="20.3" x2="83.5" y2="14.3" stroke="var(--ink)" stroke-width="1.1"/>
        <line x1="88.5" y1="14.3" x2="94.5" y2="20.3" stroke="var(--ink)" stroke-width="1.1"/>
      </g>
      <g class="icon-phone">
        <circle cx="126" cy="15" r="14.5" fill="var(--ink)"/>
        <path d="M119.5,9.5 c1.2,-1.4 2.4,-1.2 3,-0.2 l1.6,2.6 c0.5,0.9 0.2,1.6 -0.6,2.2 l-0.8,0.6 c0.8,1.9 2.3,3.4 4.2,4.2 l0.6,-0.8 c0.6,-0.8 1.3,-1.1 2.2,-0.6 l2.6,1.6 c1,0.6 1.2,1.8 -0.2,3 c-1.6,1.4 -3.6,1.6 -6.2,0.2 c-3.2,-1.7 -5.6,-4.1 -7.3,-7.3 c-1.4,-2.6 -1.2,-4.6 0.2,-6.2 z" fill="#fff"/>
        <path d="M126.5,9.2 a5.5,5.5 0 0 1 4.3,4.3" fill="none" stroke="#fff" stroke-width="1.2" stroke-linecap="round"/>
        <path d="M126.8,6.2 a8.5,8.5 0 0 1 7,7" fill="none" stroke="#fff" stroke-width="1.2" stroke-linecap="round"/>
      </g>
    </svg>

    <p class="contact-line contact-email">prattdq47@mailvessa.com</p>
    <p class="contact-line contact-phone">703-555-0142</p>
  </div>
</body>
</html>
```